Velmarotix - world unique technology for better life - please let them know who am i at first sight

We need a new business card for company which is a provider of unique crystal based technology suitable for all living being. For more information and final design you can use our brochure (our colours are black and blue from brochure).
We use Verdana font

Industry/Entity Type

Business

Contact Information for Business Card

regular dimension

Font styles to use
Other font styles liked:
• Verdana

Requirements
Must have
• Logo
• name
• function/position
• phone
• mobile
• e-mail
• adress
Nice to have
• inovative design (technology directed)

```html
<!DOCTYPE html>
<html lang="en">
<head>
<meta charset="utf-8">
<title>Velmarotix business card</title>
<link href="https://fonts.googleapis.com/css2?family=Noto+Sans:wght@400;700&display=swap" rel="stylesheet">
<style>
  :root {
    --brand-blue: #12a3e3;
    --brand-black: #050505;
    --ring-grey: #9aa3a8;
    --paper-white: #ffffff;
    --backdrop: #e6e8ea;
  }
  html, body {
    margin: 0;
    width: 1200px;
    height: 948px;
    overflow: hidden;
    background: var(--backdrop);
    font-family: Verdana, "Noto Sans", sans-serif;
  }
  .sheet {
    position: relative;
    width: 1200px;
    height: 948px;
  }
  .card {
    position: absolute;
    left: 280px;
    width: 640px;
    height: 366px;
    overflow: hidden;
    box-shadow: 0 6px 18px rgba(0,0,0,0.18);
  }
  .card-front { top: 70px; background: var(--brand-black); }
  .card-back  { top: 512px; background: var(--brand-blue); }

  .front-art { position: absolute; inset: 0; }

  .front-logo {
    position: absolute;
    left: 44px;
    top: 150px;
    display: flex;
    align-items: center;
    gap: 12px;
    color: var(--brand-blue);
  }
  .logo-dot {
    width: 46px;
    height: 46px;
    border-radius: 50%;
    background: var(--brand-blue);
  }
  .logo-words { line-height: 1; }
  .logo-name {
    font-size: 30px;
    letter-spacing: 1px;
    text-transform: uppercase;
  }
  .logo-tagline {
    margin-top: 6px;
    font-size: 10px;
    letter-spacing: 5.2px;
    text-transform: uppercase;
  }

  .contact {
    position: absolute;
    left: 408px;
    top: 58px;
    color: var(--paper-white);
  }
  .person-name {
    font-weight: 700;
    font-size: 21px;
    margin: 0;
  }
  .person-role {
    font-size: 15px;
    margin: 2px 0 16px;
  }
  .contact-list {
    list-style: none;
    margin: 0;
    padding: 0;
    font-size: 12.5px;
  }
  .contact-list li {
    display: flex;
    align-items: center;
    gap: 8px;
    height: 22px;
  }
  .contact-icon { width: 14px; height: 14px; flex: none; }
  .address {
    margin-top: 12px;
    font-size: 13.5px;
    line-height: 1.35;
  }

  .back-web {
    position: absolute;
    left: 52px;
    top: 44px;
    color: var(--paper-white);
    font-size: 14px;
    letter-spacing: 3px;
  }
  .back-logo {
    position: absolute;
    left: 0;
    right: 0;
    top: 150px;
    display: flex;
    justify-content: center;
    align-items: center;
    gap: 14px;
    color: var(--paper-white);
  }
  .back-logo .logo-dot { background: var(--paper-white); width: 58px; height: 58px; }
  .back-logo .logo-name { font-size: 34px; }
</style>
</head>
<body>
<main class="sheet">

  <section class="card card-front" aria-label="Business card front">
    <svg class="front-art" width="640" height="366" viewBox="0 0 640 366" aria-hidden="true">
      <circle cx="700" cy="150" r="350" fill="none" stroke="var(--ring-grey)" stroke-width="5"/>
      <circle cx="700" cy="150" r="340" fill="var(--brand-blue)"/>
    </svg>

    <div class="front-logo">
      <span class="logo-dot"></span>
      <div class="logo-words">
        <div class="logo-name">Velmarotix</div>
        <div class="logo-tagline">Technologies</div>
      </div>
    </div>

    <div class="contact">
      <p class="person-name">Mira Kostanjevac</p>
      <p class="person-role">Founder and CEO</p>
      <ul class="contact-list">
        <li>
          <svg class="contact-icon" viewBox="0 0 14 14" aria-label="Phone"><circle cx="7" cy="7" r="7" fill="#fff"/><path d="M4.3 3.6l1.3-.3.7 1.8-.9.7a5 5 0 0 0 2.8 2.8l.7-.9 1.8.7-.3 1.3c-3.3.3-6.4-2.8-6.1-6.1z" fill="var(--brand-blue)"/></svg>
          014-552-7310
        </li>
        <li>
          <svg class="contact-icon" viewBox="0 0 14 14" aria-label="Mobile"><circle cx="7" cy="7" r="7" fill="#fff"/><rect x="4.8" y="3" width="4.4" height="8" rx="0.8" fill="var(--brand-blue)"/><rect x="5.6" y="4" width="2.8" height="5" fill="#fff"/></svg>
          014-552-7310
        </li>
        <li>
          <svg class="contact-icon" viewBox="0 0 14 14" aria-label="Email"><circle cx="7" cy="7" r="7" fill="#fff"/><rect x="3.3" y="4.5" width="7.4" height="5" fill="var(--brand-blue)"/><path d="M3.3 4.5L7 7.4l3.7-2.9" fill="none" stroke="#fff" stroke-width="0.8"/></svg>
          info@velmarotix.cu
        </li>
        <li>
          <svg class="contact-icon" viewBox="0 0 14 14" aria-label="Website"><circle cx="7" cy="7" r="7" fill="#fff"/><circle cx="7" cy="7" r="3.8" fill="none" stroke="var(--brand-blue)" stroke-width="0.9"/><path d="M3.2 7h7.6M7 3.2c-1.6 2-1.6 5.6 0 7.6M7 3.2c1.6 2 1.6 5.6 0 7.6" fill="none" stroke="var(--brand-blue)" stroke-width="0.8"/></svg>
          www.velmarotix.cu
        </li>
      </ul>
      <div class="address">Street Name, City Name<br>Zipcode- 01234</div>
    </div>
  </section>

  <section class="card card-back" aria-label="Business card back">
    <div class="back-web">www.velmarotix.cu</div>
    <div class="back-logo">
      <span class="logo-dot"></span>
      <span class="logo-name">Velmarotix</span>
    </div>
  </section>

</main>
</body>
</html>
```